Business card for medical clinic

I need an upmarket, modern medical/health business card for my clinic

Contact Information for Business Card

name, address, email, qr code

```html
<!DOCTYPE html>
<html lang="en">
<head>
<meta charset="utf-8">
<title>Meridian Care Clinic – Business Card</title>
<link rel="stylesheet" href="https://fonts.googleapis.com/css2?family=Montserrat:wght@400;500;800&display=swap">
<style>
  :root {
    --stage: #1b1b1d;
    --sky: #27a9e3;
    --ocean: #136fa3;
    --navy: #1f3f6e;
    --ink: #141414;
    --paper: #ffffff;
    --accent: #1e8fd1;
    --accent-deep: #1c4f86;
  }
  * { margin: 0; padding: 0; box-sizing: border-box; }
  html, body { width: 1200px; height: 880px; overflow: hidden; }
  body {
    background: var(--stage);
    font-family: "Montserrat", sans-serif;
    position: relative;
  }
  .card {
    position: absolute;
    width: 560px;
    height: 320px;
    border-radius: 26px;
    overflow: hidden;
  }
  /* Front */
  .card-front {
    left: 110px;
    top: 90px;
    background: linear-gradient(160deg, var(--sky) 0%, var(--sky) 35%, var(--ocean) 75%, var(--navy) 100%);
    display: flex;
    align-items: center;
    justify-content: center;
    gap: 18px;
  }
  .brand-dot {
    width: 26px; height: 26px;
    border-radius: 50%;
    border: 3px solid var(--paper);
  }
  .brand-name {
    color: var(--paper);
    font-weight: 500;
    font-size: 30px;
    letter-spacing: 4px;
    text-transform: uppercase;
  }
  /* Back */
  .card-back {
    left: 530px;
    top: 470px;
    background: var(--ink);
  }
  .back-disc {
    position: absolute;
    left: 285px;
    top: -90px;
    width: 400px;
    height: 400px;
    border-radius: 50%;
    background: var(--paper);
  }
  .back-info {
    position: absolute;
    left: 34px;
    top: 30px;
    color: var(--paper);
  }
  .back-brand {
    display: flex; align-items: center; gap: 8px;
    color: var(--accent);
    font-weight: 500;
    font-size: 12px;
    letter-spacing: 2px;
    text-transform: uppercase;
    margin-bottom: 26px;
  }
  .back-brand .brand-dot { width: 14px; height: 14px; border: 2px solid var(--accent); }
  .person { position: relative; padding-left: 18px; margin-bottom: 18px; }
  .person::before {
    content: ""; position: absolute; left: 0; top: 4px;
    width: 7px; height: 42px;
    background: linear-gradient(180deg, var(--accent-deep), var(--accent));
  }
  .person-name {
    font-weight: 800;
    font-size: 24px;
    color: var(--accent);
    letter-spacing: 0.5px;
  }
  .person-role { font-size: 14px; margin-top: 2px; }
  .address { font-size: 14px; line-height: 1.45; margin: 0 0 14px 18px; }
  .contacts { list-style: none; margin-left: 0; font-size: 14px; }
  .contacts li { display: flex; align-items: center; gap: 8px; line-height: 1.55; }
  .contacts svg { width: 12px; height: 12px; fill: var(--accent); flex: none; }
</style>
</head>
<body>
  <section class="card card-front">
    <span class="brand-dot"></span>
    <span class="brand-name">Meridian Care Clinic</span>
  </section>

  <section class="card card-back">
    <div class="back-disc"></div>
    <div class="back-info">
      <div class="back-brand"><span class="brand-dot"></span>Meridian Care Clinic</div>
      <div class="person">
        <div class="person-name">DANIEL HART</div>
        <div class="person-role">Managing Director</div>
      </div>
      <p class="address">48 Harbor Lane, Westfield<br>Ohio, Zip 4410</p>
      <ul class="contacts">
        <li><svg viewBox="0 0 24 24"><path d="M6.6 10.8a15 15 0 0 0 6.6 6.6l2.2-2.2a1 1 0 0 1 1-.25 11.4 11.4 0 0 0 3.6.57 1 1 0 0 1 1 1V20a1 1 0 0 1-1 1A17 17 0 0 1 3 4a1 1 0 0 1 1-1h3.5a1 1 0 0 1 1 1c0 1.25.2 2.45.57 3.57a1 1 0 0 1-.25 1z"/></svg>555 018 204</li>
        <li><svg viewBox="0 0 24 24"><path d="M2 5h20v14H2zm2 2v.5l8 5 8-5V7l-8 5z"/></svg>info@meridiancare.com</li>
        <li><svg viewBox="0 0 24 24"><circle cx="12" cy="12" r="10"/></svg>www.meridiancare.com</li>
      </ul>
    </div>
  </section>
</body>
</html>
```